Animal Eye Clinic needs a Business card

We are a new veterinary ophthalmology practice (Ridgeline Pet Vision Care) and we need a business card designed. We only see animal eyes - we are not a regular veterinary clinic. We already have a logo. We are looking for a professional, good looking business card to hand out to our clients. We are looking for something simple but professional and contemporary. Our logo is likely the only picture/graphic that needs to be on the card.
Updates

Contact Information for Business Card

Delia Vossman, BSc, DVM, MSc, DipACVO
Veterinary Ophthalmologist

Phone: 250.418.3927
Email: ridgelinepetvisioncare@mailbox-example.net
Website: ridgelinepetvisioncare-example.net
Address: 1874 Thornbury Rd
Kelowna, BC, V1X 4M9

Colors

Designer to choose colors to be used in the design.

Requirements
Must have
• Our logo (attached)

```html
<!DOCTYPE html>
<html lang="en">
<head>
<meta charset="utf-8">
<title>Ridgeline Pet Vision Care – Business Card</title>
<link rel="stylesheet" href="https://fonts.googleapis.com/css2?family=Roboto:wght@300;400;500;700&display=swap">
<style>
  :root {
    --teal: #0e97a8;
    --grey: #7d7d7d;
    --text-grey: #6a6a6a;
    --paper: #ffffff;
    --stage: #2a2a2a;
  }
  * { box-sizing: border-box; margin: 0; padding: 0; }
  html, body {
    width: 1200px; height: 852px; overflow: hidden;
    background: var(--stage);
    font-family: "Roboto", Arial, sans-serif;
  }
  .card {
    position: absolute;
    width: 600px; height: 340px;
    background: var(--paper);
    box-shadow: 0 10px 30px rgba(0,0,0,.45);
    overflow: hidden;
  }
  .card--front { left: 60px; top: 60px; }
  .card--back { left: 540px; top: 452px; }

  .brand {
    display: flex; align-items: center; gap: 12px;
    color: var(--teal);
    font-weight: 500;
    text-transform: uppercase;
    line-height: 1;
    white-space: nowrap;
  }
  .brand__dot {
    width: 14px; height: 14px; border-radius: 50%;
    background: var(--teal); flex: none;
  }
  .card--front .brand {
    position: absolute; left: 0; right: 0; top: 154px;
    justify-content: center; font-size: 26px; letter-spacing: .5px;
  }
  .card--back .brand {
    position: absolute; left: 30px; top: 72px;
    font-size: 17px; letter-spacing: .3px; gap: 9px;
  }
  .card--back .brand__dot { width: 11px; height: 11px; }

  .person {
    position: absolute; right: 26px; top: 26px; text-align: right;
  }
  .person__name {
    color: var(--teal); font-size: 27px; font-weight: 400; line-height: 1.15;
  }
  .person__creds, .person__role {
    color: var(--text-grey); font-size: 11.5px; font-weight: 400;
    letter-spacing: .4px; line-height: 1.45;
  }

  .wave { position: absolute; inset: 0; width: 100%; height: 100%; }

  .contact {
    position: absolute; right: 22px; top: 168px;
    list-style: none; text-align: right;
    color: var(--paper); font-size: 11.5px; line-height: 1.55;
    white-space: nowrap;
  }
  .contact li { display: flex; justify-content: flex-end; align-items: center; gap: 6px; }
  .contact__gap { margin-top: 5px; }
  .contact svg { width: 10px; height: 10px; flex: none; }
  .contact strong { font-weight: 700; }
</style>
</head>
<body>

<section class="card card--front" aria-label="Business card front">
  <div class="brand"><span class="brand__dot"></span>Ridgeline Pet Vision Care</div>
</section>

<section class="card card--back" aria-label="Business card back">
  <svg class="wave" viewBox="0 0 600 340" aria-hidden="true">
    <path d="M0,300 C140,298 220,268 275,200 C315,150 345,125 380,112"
          fill="none" stroke="var(--grey)" stroke-width="7"/>
    <path d="M0,318 C160,312 250,272 305,195 C365,112 450,94 600,100 L600,340 L0,340 Z"
          fill="var(--teal)"/>
    <path d="M90,330 C210,318 275,275 325,205 C380,130 440,112 540,104"
          fill="none" stroke="var(--paper)" stroke-width="4"/>
  </svg>

  <div class="brand"><span class="brand__dot"></span>Ridgeline Pet Vision Care</div>

  <div class="person">
    <h1 class="person__name">Delia Vossman</h1>
    <p class="person__creds">BSc, DVM, MSc, DipACVO</p>
    <p class="person__role">Veterinary Ophthalmologist</p>
  </div>

  <ul class="contact">
    <li>Address: 1874 Thornbury Rd</li>
    <li>Kelowna, BC, V1X 4M9</li>
    <li class="contact__gap">250.418.3927
      <svg viewBox="0 0 10 10"><path d="M2 1 L3.6 1 L4.3 3 L3.2 3.8 C3.8 5 5 6.2 6.2 6.8 L7 5.7 L9 6.4 L9 8 C9 8.6 8.5 9 8 9 C4.5 9 1 5.5 1 2 C1 1.5 1.4 1 2 1 Z" fill="#fff"/></svg>
    </li>
    <li>ridgelinepetvisioncare@mailbox-example.net
      <svg viewBox="0 0 10 10"><rect x="1" y="2.2" width="8" height="5.6" fill="none" stroke="#fff" stroke-width="1"/><path d="M1 2.4 L5 5.5 L9 2.4" fill="none" stroke="#fff" stroke-width="1"/></svg>
    </li>
    <li><span>www.<strong>ridgelinepetvisioncare-example.net</strong></span>
      <svg viewBox="0 0 10 10"><circle cx="5" cy="5" r="4" fill="none" stroke="#fff" stroke-width="1"/><ellipse cx="5" cy="5" rx="1.7" ry="4" fill="none" stroke="#fff" stroke-width=".8"/><path d="M1 5 H9" stroke="#fff" stroke-width=".8"/></svg>
    </li>
  </ul>
</section>

</body>
</html>
```